Forensic Document Examiner, looking for contemporary update to my stationery design.

Looking for professional, classy logo design for stationery and business cards. My current stationery and business card is attached.I believe a logo image makes a header section interesting, so an intriguing design of a pen, feathered pen, microscope, magnifying glass, etc., would be appropriate. I have been in the business for over 30 years. I leave ideas to the imagination of the designer.My work involves mainly, the comparison of signatures and handwriting. I also resolve alterations, obliterations, and work as shown on my website: www.documentexaminer.infoThe image produced will be printed on quality white stationery and envelopes. The stationery will be photocopied by my clients, so the images should be reproducible. The business cards may be designed in other than white.

Target Market(s)

Attorneys

Font styles to use
Sans Serif

Colors

Designer to choose colors to be used in the design.

Requirements
Must have
• Image suitable for white stationery and photocopying.
• Classy logo and image; no casual fonts.
Nice to have
• Intriguing, contemporary design incorporating a relevant logo to my work.

```html
<!DOCTYPE html>
<html lang="en">
<head>
<meta charset="utf-8">
<title>Martin R. Hale – Notebook Cover</title>
<link rel="stylesheet" href="https://fonts.googleapis.com/css2?family=Crimson+Pro:ital,wght@0,600;1,400;1,600&display=swap">
<style>
  :root {
    --page-bg: #c4c4c6;
    --cover-bg: #eeeeef;
    --cover-top: #dadadb;
    --ink: #29246a;
    --band-top: #403a86;
    --band-bottom: #2b2663;
    --silver: #b9bbc0;
    --silver-light: #e4e5e8;
    --photo-light: #e9e9ea;
    --photo-dark: #6f6f73;
    --white: #ffffff;
  }
  * { margin: 0; padding: 0; box-sizing: border-box; }
  html, body {
    width: 1157px;
    height: 1200px;
    overflow: hidden;
    background: var(--page-bg);
  }
  .cover {
    position: absolute;
    left: 228px;
    top: 40px;
    width: 700px;
    height: 1120px;
    background: var(--cover-bg);
    border-radius: 0 42px 42px 0;
    overflow: hidden;
  }
  .cover__header-photo {
    position: absolute;
    left: 0;
    top: 0;
    width: 100%;
    height: 220px;
    background: linear-gradient(180deg, var(--cover-top) 0%, var(--cover-top) 45%, var(--cover-bg) 100%);
  }
  .cover__wave {
    position: absolute;
    left: 0;
    top: 0;
    width: 700px;
    height: 1120px;
  }
  .identity {
    position: absolute;
    left: 90px;
    top: 400px;
    display: flex;
    align-items: center;
    gap: 26px;
  }
  .identity__mark {
    width: 22px;
    height: 22px;
    border-radius: 50%;
    background: var(--ink);
    flex: none;
  }
  .identity__name {
    font-family: "Crimson Pro", Georgia, serif;
    font-weight: 600;
    font-size: 52px;
    line-height: 1;
    color: var(--ink);
    letter-spacing: 0.2px;
  }
  .identity__role {
    font-family: "Crimson Pro", Georgia, serif;
    font-style: italic;
    font-weight: 400;
    font-size: 27px;
    line-height: 1;
    color: var(--ink);
    margin-top: 12px;
  }
  .footer-band {
    position: absolute;
    left: 0;
    bottom: 0;
    width: 100%;
    height: 50px;
    background: linear-gradient(180deg, var(--band-top), var(--band-bottom));
    display: flex;
    align-items: center;
    justify-content: center;
  }
  .footer-band__url {
    font-family: "Crimson Pro", Georgia, serif;
    font-style: italic;
    font-weight: 600;
    font-size: 19px;
    color: var(--white);
    letter-spacing: 0.3px;
  }
</style>
</head>
<body>
  <main class="cover">
    <div class="cover__header-photo" role="img" aria-label="Faint greyscale photo of a hand holding a magnifying glass"></div>

    <svg class="cover__wave" viewBox="0 0 700 1120" xmlns="http://www.w3.org/2000/svg">
      <defs>
        <linearGradient id="nib-photo" x1="0" y1="1" x2="1" y2="0">
          <stop offset="0" stop-color="var(--photo-light)"/>
          <stop offset="0.55" stop-color="#d3d3d5"/>
          <stop offset="1" stop-color="var(--photo-dark)"/>
        </linearGradient>
        <linearGradient id="silver-sheen" x1="0" y1="1" x2="1" y2="0">
          <stop offset="0" stop-color="var(--silver)"/>
          <stop offset="0.5" stop-color="var(--silver-light)"/>
          <stop offset="1" stop-color="var(--silver)"/>
        </linearGradient>
      </defs>
      <path role="img" aria-label="Photo of a fountain pen nib writing ink strokes on paper"
            d="M0,1072 L0,1062 C140,900 330,858 505,828 C615,805 680,720 700,585 L700,1072 Z"
            fill="url(#nib-photo)"/>
      <path d="M0,1060 C140,896 330,854 505,824 C615,801 680,716 700,580"
            fill="none" stroke="url(#silver-sheen)" stroke-width="10"/>
      <path d="M0,1048 C150,884 335,846 505,816 C612,794 676,712 696,585"
            fill="none" stroke="var(--white)" stroke-width="3" opacity="0.8"/>
    </svg>

    <section class="identity">
      <span class="identity__mark"></span>
      <div class="identity__text">
        <h1 class="identity__name">Martin R. Hale</h1>
        <p class="identity__role">Forensic Document Examinar</p>
      </div>
    </section>

    <footer class="footer-band">
      <span class="footer-band__url">www.quillmarkreview.info</span>
    </footer>
  </main>
</body>
</html>
```